Event Center Website

We need a new website design for an upscale event center in Reno, Nevada. The building hosts everything from weddings to corporate events to funerals and it competitively more expensive. The overall look and feel is consistent with a Lake Tahoe aesthetic. The current site can be viewed at www.themaplehallevents.com. They are looking for a major upgrade. A sample site they like is www.cliffsidelodgestay.com. We have new photography available (some attached). The site should be very visual. A site map is attached as well for direction on what elements the site should include as well as labels for navigation. I am looking for a home page and sample interior page. Any questions, let me know. Thanks.
Updates

I have added some photography of the center itself for use rather than stock photography. Thanks!

Target Market(s)

Brides, professionals, high-income

Industry/Entity Type

Building

Requirements
Must have
• See site map

```html
<!DOCTYPE html>
<html lang="en">
<head>
<meta charset="utf-8">
<title>About Us – The Maple Hall</title>
<link href="https://fonts.googleapis.com/css2?family=Ubuntu:ital,wght@0,300;0,400;0,500;1,300;1,400&display=swap" rel="stylesheet">
<style>
:root{
  --brown-dark:#4a230d;
  --brown:#5a2e12;
  --brown-mid:#7a3f0a;
  --orange:#cf7a1c;
  --accent:#b06a2e;
  --cream:#f5e6c4;
  --cream-light:#f0e8d6;
  --card:#f3f3f3;
  --card-border:#dcdcdc;
  --text:#4a4a4a;
}
*{box-sizing:border-box;margin:0;padding:0}
html,body{width:1200px;height:1123px;overflow:hidden;background:#fff;font-family:'Ubuntu',sans-serif}
.page{position:relative;width:1200px;height:1123px}
.hero{position:absolute;left:0;top:0;width:1200px;height:157px;
  background:linear-gradient(90deg,#6b3a12 0%,#c98a3a 20%,#e8c89a 35%,#8a5a22 50%,#e8c89a 65%,#c98a3a 80%,#6b3a12 100%)}
.utility{position:absolute;left:849px;top:0;width:227px;height:52px;background:var(--brown-dark);
  display:flex;align-items:center;justify-content:center;color:#fff;font-size:15px}
.utility span.sep{width:2px;height:26px;background:#fff;margin:0 26px}
.mainnav{position:absolute;left:100px;top:52px;width:976px;height:58px;background:var(--cream);display:flex;align-items:center}
.brand{font-size:22px;font-weight:500;color:var(--brown);margin-left:8px;width:198px;letter-spacing:.5px}
.mainnav ul{list-style:none;display:flex;gap:34px;font-size:14px;font-weight:500;color:var(--brown-dark)}
.titleband{position:absolute;left:0;top:157px;width:1200px;height:70px;background:var(--cream-light);border-bottom:2px solid var(--brown-dark)}
.titleband h1{position:absolute;left:167px;top:18px;font-size:27px;font-weight:500;color:var(--brown)}
.crumb{position:absolute;right:150px;top:26px;font-size:16px;font-weight:500;color:var(--brown-dark)}
.crumb em{font-style:normal;color:var(--accent)}
.intro h2{position:absolute;left:0;width:1200px;top:254px;text-align:center;font-size:34px;font-weight:500;color:var(--brown)}
.intro .rule{position:absolute;left:562px;top:312px;width:76px;height:2px;background:var(--brown)}
.intro p{position:absolute;left:120px;top:329px;width:960px;text-align:center;font-size:19px;font-weight:300;line-height:26px;color:var(--text)}
.card{position:absolute;width:463px;height:222px;background:var(--card);border:1px solid var(--card-border)}
.card .photo{position:absolute;left:6px;top:20px;width:127px;height:127px;border-radius:50%;border:3px solid #9c9c9c;
  background:radial-gradient(circle at 50% 40%,#d9b8a0 0%,#a0735a 45%,#e8e8e8 75%)}
.card .name{position:absolute;left:0;width:146px;top:162px;text-align:center;font-size:20px;color:var(--brown)}
.card h3{position:absolute;left:150px;top:26px;font-size:17px;font-weight:400;color:var(--brown)}
.card blockquote{position:absolute;left:153px;top:52px;width:300px;font-size:14px;font-style:italic;font-weight:400;line-height:25.7px;color:var(--brown)}
.footer{position:absolute;left:0;top:956px;width:1200px;height:167px;background:var(--cream)}
.signup{position:absolute;left:131px;top:40px;width:340px;height:60px;background:var(--brown-mid);display:flex;align-items:center}
.signup .label{color:#fff;font-size:14px;margin-left:9px;width:232px}
.signup svg{margin-right:10px}
.signup .send{position:absolute;right:0;top:0;width:56px;height:60px;background:var(--orange);border-radius:0 4px 4px 0;color:#fff;font-size:14px;display:flex;align-items:center;justify-content:center}
.contact{position:absolute;left:495px;top:41px;width:362px;height:58px;background:var(--brown-dark);border-radius:3px;color:#fff;font-size:12.5px}
.contact .addr{position:absolute;left:11px;top:11px;line-height:21px;white-space:nowrap}
.contact .div{position:absolute;left:150px;top:0;width:1px;height:58px;background:#7a4a2a}
.contact .lines{position:absolute;left:159px;top:8px;line-height:24px;white-space:nowrap}
.contact .lines b{font-weight:400;color:var(--orange);margin-right:6px}
.social{position:absolute;left:887px;top:41px;width:189px;height:59px;background:#6b3410;border-radius:3px;display:flex;align-items:center;justify-content:center;gap:12px}
.social span{width:29px;height:29px;border-radius:3px}
.footnav{position:absolute;left:0;top:128px;width:1200px;display:flex;justify-content:center;gap:28px;list-style:none;font-size:14px;color:var(--brown-dark)}
</style>
</head>
<body>
<div class="page">
  <div class="hero" role="img" aria-label="Event hall ceiling with draped fabric and a chandelier"></div>
  <div class="utility"><span>FAQ</span><span class="sep"></span><span>TESTIMONIAL</span></div>
  <nav class="mainnav">
    <div class="brand">The Maple Hall</div>
    <ul><li>ABOUT US</li><li>GALLERY</li><li>WEDDING</li><li>MEETINGS</li><li>OTHER EVENTS</li><li>CATERING</li><li>MENUS</li></ul>
  </nav>
  <div class="titleband"><h1>ABOUT US</h1><div class="crumb">HOME / <em>ABOUT US</em></div></div>
  <section class="intro">
    <h2>About Us</h2><div class="rule"></div>
    <p>The staff at The Maple Hall is experienced, talented, and committed to creating a carefree and expertly organized event.&nbsp; Our seasoned staff will assist you in planning and coordinating a successful event with gourmet catering anda full service bar.</p>
  </section>
  <article class="card" style="left:124px;top:447px">
    <div class="photo" role="img" aria-label="Portrait of staff member Marla"></div>
    <div class="name">Marla</div>
    <h3>Lorem Ipsum is simply dummy text of</h3>
    <blockquote>“The Maple Hall is such a beautiful venue, that I was immediately attracted to it as soon as I walked through the doors. Since I have been here I can see how the beauty of the space in combination with our inviting food creates lasting memories for our guests.”</blockquote>
  </article>
  <article class="card" style="left:614px;top:447px">
    <div class="photo" role="img" aria-label="Portrait of staff member Devon"></div>
    <div class="name">Devon</div>
    <h3>Lorem Ipsum is simply dummy text of</h3>
    <blockquote>“The Maple Hall has allowed me to express my creativity in new and different ways and connect on a personal level with our guests.”-</blockquote>
  </article>
  <article class="card" style="left:124px;top:695px">
    <div class="photo" role="img" aria-label="Portrait of staff member Colette"></div>
    <div class="name">Colette</div>
    <h3>Lorem Ipsum is simply dummy text of</h3>
    <blockquote>“What I enjoy most is the diversity and ever changing trends of our business.”</blockquote>
  </article>
  <article class="card" style="left:614px;top:695px">
    <div class="photo" role="img" aria-label="Portrait of staff member Priya"></div>
    <div class="name">Priya</div>
    <h3>Lorem Ipsum is simply dummy text of</h3>
    <blockquote>“I believe in creating a professional, inviting atmosphere where guests will enjoy amazing food served by welcoming staff.”-</blockquote>
  </article>
  <footer class="footer">
    <div class="signup">
      <span class="label">ENTER YOUR EMAIL</span>
      <svg width="32" height="28" viewBox="0 0 32 28" aria-hidden="true"><path d="M2 11 L16 2 L30 11 V26 H2 Z" fill="#fff"/><path d="M2 11 L16 20 L30 11 M2 26 L13 17 M30 26 L19 17" stroke="#7a3f0a" stroke-width="1.5" fill="none"/><circle cx="16" cy="9" r="4" fill="none" stroke="#7a3f0a" stroke-width="1.5"/></svg>
      <div class="send">SEND</div>
    </div>
    <div class="contact">
      <div class="addr">218 Aspen Ridge Road<br>Reno, NV 89509</div>
      <div class="div"></div>
      <div class="lines"><b>Phone:</b>775-555-0148<br><b>Email:</b>info@maplehallreno.com</div>
    </div>
    <div class="social">
      <span style="background:#3b5998"></span><span style="background:#29a9e1"></span><span style="background:#d8251b"></span><span style="background:#f58220"></span>
    </div>
    <ul class="footnav"><li>ABOUT US</li><li>GALLERY</li><li>WEDDING</li><li>MEETINGS</li><li>OTHER EVENTS</li><li>CATERING</li><li>MENUS</li></ul>
  </footer>
</div>
</body>
</html>
```